Friendly website/webshop needed for small family store

Hello .. I really need a website that is easy to use as I have no experience with this at all. ..
My shop is called quillmoss and I had a fantastic logo from craft forge - I asked for something mid century modern and I love it. I will attach . There might be some development around the logo now for various paraphernalia ( stickers , printed tissue paper carrier bags etc.. ) I would also like some sort of help with a slogan such as 'sing your prettiest song' as in,  live your best life etc..  but I'm not sure if this is a little trite .... ? but it would be nice to link the quillmoss with a little Motto.    If I need to pay extra for this - please could you let me know ... I'm happy to add on payment ..
As you can see the only LOGO colours really are grey black and orange .. so I would like some ideas to expand on the bird  to bring in some more colours.....  the tag line flower.children.home I would like to drop..
* the original brief included flowers on the tag line  because at the time we were also a florist . we now just sell dried flowers
My shop is in the beautiful town of Malvern, we have lots of tourist that come to walk the hills and enjoy nature - it's a family and dog friendly sort of town and we are a dog and family friendly sort of shop :-) It's a relaxed space that focuses on beautiful handmade items such as baskets & wooden utensils  from Africa, textiles from India and ceramics from France, Portugal and Italy.  We have a lovely section for children that sells beautiful soft toys from Charmel Duvo and the wonderful mice family and bunnies from Tornby.
We stock OBRETI homeware which is lovely and earthy and natural.
We would like to communicate the value of buying thoughtfully  and conscientiously, of building a beautiful home whilst investing in & supporting makers world wide. We don't sell anything that can't be repurposed, recycled etc..
Thank you

```html
<!DOCTYPE html>
<html lang="en">
<head>
<meta charset="utf-8">
<title>quillmoss — Live Your Best Life</title>
<link href="https://fonts.googleapis.com/css2?family=Poppins:ital,wght@0,300;0,400;0,500;0,600;0,700;1,400&family=Rammetto+One&display=swap" rel="stylesheet">
<style>
:root{
  --ink:#2a2a2a;
  --dark:#2b2b2b;
  --white:#ffffff;
  --soft:#f3f3f3;
  --salmon:#d18b7d;
  --slate:#6f7b9a;
  --teal:#77b2c5;
  --line:#dcdcdc;
  --muted:#8a8a8a;
}
*{box-sizing:border-box;margin:0;padding:0}
html,body{width:1200px;height:4827px;overflow:hidden}
body{position:relative;background:var(--white);font-family:"Poppins",sans-serif;color:var(--ink)}
.abs{position:absolute}
.display{font-family:"Rammetto One",sans-serif;letter-spacing:1px;text-transform:uppercase}
.btn{position:absolute;background:var(--salmon);color:var(--white);border-radius:30px;display:flex;align-items:center;justify-content:center;font-family:"Rammetto One",sans-serif;font-size:17px;text-transform:uppercase;letter-spacing:1px}

/* header */
.site-header{left:0;top:0;width:1200px;height:120px}
.brand{left:75px;top:20px;width:140px;height:92px}
.brand-dot{position:absolute;left:46px;top:0;width:42px;height:42px;border-radius:50%;background:var(--slate)}
.brand-name{position:absolute;left:0;top:44px;font-weight:700;font-size:27px;color:var(--dark);letter-spacing:-.5px}
.brand-tag{position:absolute;left:1px;top:80px;font-size:10px;color:var(--salmon);letter-spacing:.4px}
.phone{left:518px;top:48px;font-size:22px;font-weight:500;color:var(--slate);letter-spacing:1px;display:flex;align-items:center;gap:8px}
.search{left:746px;top:38px;width:294px;height:48px;border:1px solid #cfcfcf;border-radius:24px;display:flex;align-items:center;justify-content:space-between;padding:0 16px 0 22px;font-size:13px;color:#777}
.icon-user{left:1060px;top:52px}
.icon-cart{left:1106px;top:52px}

/* nav */
.main-nav{left:0;top:120px;width:1200px;height:56px;background:var(--dark)}
.main-nav span{position:absolute;top:16px;color:var(--white);font-family:"Rammetto One",sans-serif;font-size:19px;text-transform:uppercase;letter-spacing:1px}

/* hero */
.hero{left:0;top:176px;width:1200px;height:634px;background:linear-gradient(180deg,#dfe3e8 0%,#c8ccd0 14%,#6d6e6f 32%,#9ea7ae 60%,#8a8179 100%)}
.dots{display:flex;gap:10px}
.dots i{width:12px;height:12px;border-radius:50%;background:var(--white);display:block}

/* about */
.about-title{left:75px;top:892px;font-size:42px}
.about-text{left:75px;top:966px;width:520px;font-size:16px;line-height:29.5px;color:#333}
.about-photo{left:617px;top:891px;width:508px;height:339px;border-radius:26px;background:linear-gradient(135deg,#8a7a62,#b79a83 45%,#6f5f4f)}

/* products */
.products{left:0;top:1303px;width:1200px;height:696px;background:var(--soft)}
.section-title{left:0;width:1200px;text-align:center;font-size:42px}
.card{position:absolute;width:328px;height:442px;background:var(--white);border-radius:24px}
.card .pic{position:absolute;left:24px;top:24px;width:280px;height:300px;border-radius:8px}
.card .label{position:absolute;left:0;width:100%;text-align:center;color:var(--slate);font-size:23px;line-height:30px;text-transform:uppercase;font-weight:400}
.card .sub{position:absolute;left:0;width:100%;text-align:center;color:var(--salmon);font-size:22px;line-height:34px}
.arrow{position:absolute}

/* location */
.location{left:0;top:1999px;width:1200px;height:626px;background:linear-gradient(180deg,#ffffff 0%,#e6ebee 18%,#9fa9a6 45%,#6d7764 70%,#5a5f4e 100%)}
.loc-title{left:0;top:2140px;width:1200px;text-align:center;font-size:42px;line-height:53px}
.loc-text{left:170px;top:2260px;width:860px;text-align:center;font-size:16px;line-height:29px;color:#1f1f1f}

/* handmade */
.handmade .card{border:2px solid #e3e3e3}
/* testimonials */
.testimonials{left:0;top:3347px;width:1200px;height:409px;background:var(--teal)}
.testi-title{left:0;top:3408px;width:1200px;text-align:center;font-size:42px;color:var(--white)}
.testi-quote{left:150px;top:3484px;width:900px;text-align:center;color:var(--white);font-size:20px;line-height:32px}
.testi-name{left:0;top:3598px;width:1200px;text-align:center;color:var(--white);font-size:15px}
.testi-dots{left:562px;top:3672px;display:flex;gap:11px}
.testi-dots i{width:11px;height:11px;border-radius:50%;background:var(--white);display:block}
.testi-dots i:first-child{background:var(--dark)}

/* blog */
.post{position:absolute;top:3906px;width:328px}
.post .thumb{width:328px;height:223px}
.post .date{margin-top:24px;font-size:14px;font-weight:600;color:var(--salmon)}
.post .headline{margin-top:12px;font-size:25px;line-height:33px;color:#2d2d2d}

/* footer */
.site-footer{left:0;top:4365px;width:1200px;height:462px;background:var(--dark)}
.foot-brand{left:75px;top:4434px;width:260px;height:212px}
.foot-dot{position:absolute;left:80px;top:0;width:100px;height:100px;border-radius:50%;background:var(--slate)}
.foot-name{position:absolute;left:0;top:112px;font-size:50px;font-weight:700;color:#e9e9e9;letter-spacing:-1px}
.foot-tag{position:absolute;left:2px;top:182px;font-size:23px;color:#e9e9e9;letter-spacing:.5px}
.foot-col{position:absolute;top:4432px}
.foot-col h4{font-family:"Rammetto One",sans-serif;font-weight:400;font-size:17px;color:var(--white);text-transform:uppercase;letter-spacing:1px;margin-bottom:14px}
.foot-col li{list-style:none;color:#e6e6e6;font-size:15px;line-height:34px}
.news-text{font-style:italic;font-size:14px;line-height:27px;color:#cfcfcf;width:330px}
.email{left:795px;top:4541px;width:330px;height:53px;border:1px solid #8a8a8a;border-radius:27px;padding-left:24px;display:flex;align-items:center;color:#bdbdbd;font-style:italic;font-size:14px}
.subscribe{left:795px;top:4611px;width:330px;height:50px}
.foot-rule{left:0;top:4742px;width:1200px;height:1px;background:#3d3d3d}
.copyright{left:82px;top:4780px;font-size:13px;color:#e6e6e6}
.socials{left:930px;top:4774px;display:flex;gap:22px}
.socials i{width:24px;height:24px;border-radius:50%;background:#e6e6e6;display:block}
</style>
</head>
<body>

<header class="abs site-header">
  <div class="abs brand">
    <span class="brand-dot"></span>
    <span class="brand-name">quillmoss</span>
    <span class="brand-tag">LIVE YOUR BEST LIFE</span>
  </div>
  <div class="abs phone">
    <svg width="22" height="22" viewBox="0 0 24 24" fill="none" stroke="#6f7b9a" stroke-width="2"><path d="M5 3h4l2 5-3 2a11 11 0 0 0 6 6l2-3 5 2v4a2 2 0 0 1-2 2A17 17 0 0 1 3 5a2 2 0 0 1 2-2z"/></svg>
    + 144-555-0123
  </div>
  <div class="abs search">Search
    <svg width="18" height="18" viewBox="0 0 24 24" fill="none" stroke="#b8862e" stroke-width="2.5"><circle cx="10" cy="10" r="6"/><path d="M15 15l5 5"/></svg>
  </div>
  <svg class="abs icon-user" width="20" height="20" viewBox="0 0 24 24" fill="#6a6a6a"><circle cx="12" cy="8" r="4.5"/><path d="M3 21c1-5 5-7 9-7s8 2 9 7z"/></svg>
  <svg class="abs icon-cart" width="22" height="20" viewBox="0 0 24 22" fill="#6a6a6a"><path d="M1 2h4l3 12h12l3-9H7" fill="none" stroke="#6a6a6a" stroke-width="2.5"/><circle cx="9" cy="19" r="2"/><circle cx="19" cy="19" r="2"/><path d="M7 5h16l-3 9H9z"/></svg>
</header>

<nav class="abs main-nav">
  <span style="left:94px">Home</span>
  <span style="left:238px">About</span>
  <span style="left:394px">Products</span>
  <span style="left:596px">News</span>
  <span style="left:731px">Testimonials</span>
  <span style="left:964px">Contact Us</span>
</nav>

<section class="abs hero" role="img" aria-label="Photo of the shop front with large glass windows and the shop sign above">
  <div class="abs dots" style="left:588px;top:580px"><i></i><i></i><i></i></div>
</section>

<h2 class="abs display about-title">About quillmoss</h2>
<p class="abs about-text">Sed ut perspiciatis unde omnis iste natus error sit voluptatem accusantiumdoloremque laudantium, totam rem aperiam, eaque ipsa quae ab illo inventore veritatis et quasi architecto beatae vitae dicta sunt explicaboemo enim ipsam voluptatem quia voluptas sit aspernatur aut odit aut fugit, sed quia cons.</p>
<div class="btn" style="left:75px;top:1170px;width:210px;height:60px">Read More</div>
<div class="abs about-photo" role="img" aria-label="Photo of the shop interior with woven baskets, cushions and shelves"></div>

<section class="abs products">
  <h2 class="abs display section-title" style="top:72px">Our Products</h2>
  <svg class="arrow" style="left:38px;top:376px" width="22" height="34" viewBox="0 0 22 34" fill="none" stroke="#777" stroke-width="2.5"><path d="M18 2L4 17l14 15"/></svg>
  <svg class="arrow" style="left:1140px;top:376px" width="22" height="34" viewBox="0 0 22 34" fill="none" stroke="#777" stroke-width="2.5"><path d="M4 2l14 15L4 32"/></svg>
  <div class="card" style="left:75px;top:171px">
    <div class="pic" role="img" aria-label="Photo of a floral porcelain teapot with cup and saucer" style="background:radial-gradient(circle at 50% 50%,#efd9d6 0%,#f7efe9 45%,#ffffff 75%)"></div>
    <div class="label" style="top:341px">Sedut<br>Perspiciatis</div>
  </div>
  <div class="card" style="left:437px;top:171px">
    <div class="pic" role="img" aria-label="Photo of a blue plush hippo soft toy" style="background:radial-gradient(circle at 50% 50%,#9fb2d2 0%,#c9d4e6 45%,#ffffff 75%)"></div>
    <div class="label" style="top:341px">Sedut<br>Perspiciatis</div>
  </div>
  <div class="card" style="left:799px;top:171px">
    <div class="pic" role="img" aria-label="Photo of a wooden bucket with a metal handle" style="background:radial-gradient(circle at 50% 60%,#8b6a4a 0%,#c9b29a 40%,#ffffff 72%)"></div>
    <div class="label" style="top:341px">Sedut<br>Perspiciatis</div>
  </div>
</section>

<section class="abs location" role="img" aria-label="Aerial photo of the town of Malvern and its green hills"></section>
<h2 class="abs display loc-title">We located in beautiful<br>town of Malvern</h2>
<p class="abs loc-text">Sed ut perspiciatis unde omnis iste natus error sit  voluptatem  accusantiumdoloremque laudantium, totam rem aperiam, eaque ipsa quae ab illo inventore veritatis et quasi architecto beatae vitae dicta sunt explicaboemo enim ipsam voluptatem quia voluptas sit aspernatur aut</p>
<div class="btn" style="left:495px;top:2383px;width:210px;height:58px">Read More</div>

<section class="handmade">
  <h2 class="abs display section-title" style="top:2710px">Beautiful Handmade Items</h2>
  <div class="card" style="left:75px;top:2809px">
    <div class="pic" role="img" aria-label="Photo of a woven wicker basket" style="background:radial-gradient(circle at 50% 50%,#c08a4e 0%,#e6c9a3 40%,#ffffff 72%)"></div>
    <div class="label" style="top:309px">Baskets &amp; Wooden<br>Utensils</div>
    <div class="sub" style="top:373px">From Africa</div>
  </div>
  <div class="card" style="left:437px;top:2809px">
    <div class="pic" role="img" aria-label="Photo of round woven textile mats" style="background:radial-gradient(circle at 50% 50%,#a88660 0%,#dcc8ae 40%,#ffffff 72%)"></div>
    <div class="label" style="top:309px">Textiles</div>
    <div class="sub" style="top:343px">From India</div>
  </div>
  <div class="card" style="left:799px;top:2809px">
    <div class="pic" role="img" aria-label="Photo of a blue and white painted ceramic teapot" style="background:radial-gradient(circle at 50% 50%,#4e6aa0 0%,#c6d0e2 42%,#ffffff 72%)"></div>
    <div class="label" style="top:309px">Ceramics</div>
    <div class="sub" style="top:343px">From France, Portugal<br>and Italy</div>
  </div>
</section>

<section class="abs testimonials"></section>
<h2 class="abs display testi-title">Testimonials</h2>
<p class="abs testi-quote">“ Sed ut perspiciatis unde omnis iste natus error sit voluptatem accusa ntiumdoloremque laudantium, totam rem aperiam, eaque ipsa quae ab illo inventore veritatis et quasi architecto beatae vitae dicta sunt..”</p>
<p class="abs testi-name">-NAME HEADING</p>
<div class="abs testi-dots"><i></i><i></i><i></i><i></i></div>

<section class="blog">
  <h2 class="abs display section-title" style="top:3815px">Blog Posts</h2>
  <article class="post" style="left:75px">
    <div class="thumb" role="img" aria-label="Photo of colourful baskets and cushions in the shop" style="background:linear-gradient(135deg,#8c6e55,#c29c86 50%,#6e5c4c)"></div>
    <p class="date">Apri 30, 2023</p>
    <h3 class="headline" style="font-weight:400">Neque porro quisquam est, qui dolorem ipsum quia sit amet.</h3>
  </article>
  <article class="post" style="left:437px">
    <div class="thumb" role="img" aria-label="Photo of a children's corner with soft toys and treats" style="background:linear-gradient(135deg,#7c6c5e,#cfb6a8 50%,#8a6f64)"></div>
    <p class="date">Apri 30, 2023</p>
    <h3 class="headline" style="font-weight:400">Neque porro quisquam est, qui dolorem ipsum quia sit amet.</h3>
  </article>
  <article class="post" style="left:799px">
    <div class="thumb" role="img" aria-label="Photo of the shop floor with tables of homeware" style="background:linear-gradient(135deg,#6a5848,#a89078 50%,#5c4e42)"></div>
    <p class="date">Apri 30, 2023</p>
    <h3 class="headline" style="font-weight:400">Neque porro quisquam est, qui dolorem ipsum quia sit amet.</h3>
  </article>
</section>

<footer class="abs site-footer"></footer>
<div class="abs foot-brand">
  <span class="foot-dot"></span>
  <span class="foot-name">quillmoss</span>
  <span class="foot-tag">LIVE YOUR BEST LIFE</span>
</div>
<div class="foot-col" style="left:369px">
  <h4>Quick Links</h4>
  <ul><li>Home</li><li>About</li><li>Products</li><li>News</li><li>Testimonials</li><li>Contact Us</li></ul>
</div>
<div class="foot-col" style="left:576px">
  <h4>Products</h4>
  <ul><li>Nemo enim</li><li>Ipsam voluptatem</li><li>Quia voluptas</li><li>Auia non</li><li>Numquam</li></ul>
</div>
<div class="foot-col" style="left:795px">
  <h4>Newsletter Sign Up</h4>
  <p class="news-text">Quis autem vel eum iure reprehenderit qui in ea voluptate</p>
</div>
<div class="abs email">Email Address</div>
<div class="btn subscribe">Subscribe</div>
<div class="abs foot-rule"></div>
<p class="abs copyright">Copyright © 2024, Company Name  All Right reserved</p>
<div class="abs socials" aria-label="Social links"><i></i><i></i><i></i><i></i><i></i></div>

</body>
</html>
```